Baby Adoption Announcement

I'm looking for a simple, understated and modern baby adoption announcement.

The baby is a boy, but I don't want anything that is blue or particularly boyish. No storks, baby baskets, rattles, or traditional baby announcement designs. No cutesy or busy designs.

Should measure 5.25 x 8.25 inches to fit in an A9 envelope.

Simple graphics MIGHT include birds, grasses, trees, rivers. I'm open to other ideas. Text can be a single color or multi colored. Graphics are not mandatory.

Since this is text heavy, I'd like the designer to be REALLY GOOD at choosing fonts and typesetting.

Text should read:

Memory answers us bright on your face—
Impossibly, we spoke and were silent
Together before all of this. (in italics)

Tobias Aldric Pelt Ostry
Born on March 16, 2012 in Boston, MA
and entrusted to us by his birthmother, Greta.

Named Tobias, which means God is with us, after Greta’s grandfather &
Aldric, after Al and St. Aldric of Myra

Requirements
Must have
• Should measure 5.25 x 8.25 inches to fit in A9 envelope.

Should not have
• The baby is a boy, but I don't want anything that is blue or particularly boyish. No storks, baby baskets, rattles, or traditional baby announcement designs. Nothing cutesy or busy.

```html
<!DOCTYPE html>
<html lang="en">
<head>
<meta charset="utf-8">
<title>Adoption Announcement – Tobias Aldric Pelt Ostry</title>
<link rel="stylesheet" href="https://fonts.googleapis.com/css2?family=Great+Vibes&family=Sorts+Mill+Goudy&display=swap">
<style>
  :root {
    --bronze: #976817;
    --bronze-deep: #8d6217;
    --paper: #ffffff;
    --leaf: #a9b63c;
    --dragonfly: #c91f27;
    --ink-light: #ffffff;
    --backdrop: #ffffff;
  }
  * { margin: 0; padding: 0; box-sizing: border-box; }
  html, body { width: 1200px; height: 909px; overflow: hidden; background: var(--backdrop); }
  .announcement { position: relative; width: 1200px; height: 909px; }
  .announcement__art { position: absolute; inset: 0; }
  .message {
    position: absolute; left: 315px; top: 184px; width: 570px; height: 522px;
    color: var(--ink-light); text-align: center;
    font-family: "Sorts Mill Goudy", Georgia, serif;
  }
  .verse {
    position: absolute; left: 0; right: 0; top: 62px;
    font-family: "Great Vibes", cursive; font-size: 33px; line-height: 36px;
    letter-spacing: 1.5px; word-spacing: 5px;
  }
  .details { position: absolute; left: 0; right: 0; top: 212px; font-size: 22px; line-height: 35px; }
  .details__name { font-variant: small-caps; font-size: 26px; letter-spacing: 1.2px; }
  .naming { position: absolute; left: 0; right: 0; top: 341px; font-size: 22px; line-height: 35px; }
  .small-caps { font-variant: small-caps; letter-spacing: 0.6px; }
  .script-name { font-family: "Great Vibes", cursive; font-size: 27px; }
</style>
</head>
<body>
<main class="announcement">
  <svg class="announcement__art" viewBox="0 0 1200 909" width="1200" height="909">
    <defs>
      <filter id="card-shadow" x="-5%" y="-5%" width="110%" height="110%">
        <feDropShadow dx="3" dy="3" stdDeviation="3" flood-color="#000" flood-opacity="0.35"/>
      </filter>
      <linearGradient id="ornament-left-tone" x1="0" y1="0" x2="0" y2="1">
        <stop offset="0" stop-color="var(--leaf)" stop-opacity="0.18"/>
        <stop offset="0.55" stop-color="var(--leaf)" stop-opacity="0.12"/>
        <stop offset="1" stop-color="var(--bronze)" stop-opacity="0.10"/>
      </linearGradient>
      <linearGradient id="ornament-right-tone" x1="0" y1="0" x2="0" y2="1">
        <stop offset="0" stop-color="var(--leaf)" stop-opacity="0.18"/>
        <stop offset="0.6" stop-color="var(--dragonfly)" stop-opacity="0.08"/>
        <stop offset="1" stop-color="var(--bronze)" stop-opacity="0.10"/>
      </linearGradient>
    </defs>

    <rect class="card-outer" x="14" y="14" width="1168" height="874" fill="var(--bronze)" filter="url(#card-shadow)"/>
    <rect class="card-panel" x="37" y="93" width="1120" height="726" fill="var(--paper)" filter="url(#card-shadow)"/>
    <rect class="card-rule" x="50" y="113" width="1084" height="688" fill="none" stroke="var(--bronze)" stroke-width="8" filter="url(#card-shadow)"/>

    <rect class="ornament ornament--left" role="img" aria-label="Green curling vine with a red dragonfly and a dashed looping flight trail"
      x="58" y="270" width="400" height="525" fill="url(#ornament-left-tone)"/>
    <rect class="ornament ornament--right" role="img" aria-label="Green curling vine with a red dragonfly circling on a dashed flight trail"
      x="880" y="290" width="246" height="450" fill="url(#ornament-right-tone)"/>

    <rect class="message-box" x="314" y="183" width="570" height="523" rx="62" fill="var(--bronze-deep)"
      stroke="var(--paper)" stroke-width="6" stroke-dasharray="22 14" filter="url(#card-shadow)"/>
  </svg>

  <section class="message">
    <p class="verse">Memory answers us bright on your face<br>Impossibly, we spoke and were silent<br>Together before all of this</p>
    <p class="details">
      <span class="details__name">Tobias Aldric Pelt Ostry</span><br>
      Born on March 16, 2012 in Boston, MA<br>
      and entrusted to us by his birthmother, <span class="script-name">Greta</span>.
    </p>
    <p class="naming">
      Named Tobias, which means <span class="small-caps">God is with us</span><br>
      after Greta’s grandfather &amp;<br>
      <span class="small-caps">Aldric</span>, after Al and <span class="small-caps">St. Aldric of Myra</span>
    </p>
  </section>
</main>
</body>
</html>
```